QAMBRO THERAPEUTICS

physical therapy company. need a flashy image and named logo, website link, that I can also use on Letterhead and business cards. Clean, sharp, modern, eye catching. 3 colors? Some shine. Needs to stand out and not be trendy or too much cursive . Androgynous image of a human body is ok. A spine included is ok. Prefer lines to curves for font types. Warm colors but strong impact. Will need to have some contact info and border mission statement on it.
Updates

Target Market(s)

Target market is large corporations, wealthy individuals, medical doctors

Industry/Entity Type

Medical, physical therapy

Contact Information for Business Card

Name, Owner, phone, email, and website

Colors
0054AA
0677BA
7BADD7
CADEEF
E8F1F8

Requirements
Must have
• See above- something about BALANCE, wellness, strength etc
Nice to have
• Contrast, depth
Should not have
• No cursive

```html
<!DOCTYPE html>
<html lang="en">
<head>
<meta charset="utf-8">
<title>Qambro Therapeutics – Business Cards</title>
<link rel="stylesheet" href="https://fonts.googleapis.com/css2?family=Montserrat:wght@200;400;800&display=swap">
<style>
  :root {
    --backdrop: #c9cacb;
    --card-top: #7badd7;
    --card-mid: #3f93cf;
    --card-bottom: #0677ba;
    --ink-light: #ffffff;
    --art-light: #e4e6e8;
    --art-mid: #c3c7cb;
    --card-shadow: rgba(0, 0, 0, 0.35);
  }
  * { box-sizing: border-box; margin: 0; padding: 0; }
  html, body {
    width: 1200px; height: 900px; overflow: hidden;
    background: var(--backdrop);
    font-family: "Montserrat", sans-serif;
  }
  .stage {
    position: relative; width: 1200px; height: 900px;
    display: flex; flex-direction: column; align-items: center; justify-content: center; gap: 44px;
  }
  .card {
    position: relative; width: 620px; height: 354px;
    border-radius: 30px; overflow: hidden;
    background: linear-gradient(180deg, var(--card-top) 0%, var(--card-mid) 55%, var(--card-bottom) 100%);
    box-shadow: 0 10px 18px var(--card-shadow);
    color: var(--ink-light);
  }
  .figure-art {
    position: absolute; right: 0; top: 0; width: 205px; height: 100%;
    background: linear-gradient(90deg, rgba(228, 230, 232, 0) 0%, rgba(195, 199, 203, 0.75) 35%, var(--art-light) 100%);
  }
  .brand {
    position: absolute; display: flex; align-items: baseline; gap: 8px;
    white-space: nowrap;
  }
  .brand-name { font-weight: 800; font-size: 26px; letter-spacing: 0.5px; }
  .brand-tagline { font-weight: 200; font-size: 26px; letter-spacing: 1px; }
  .card--front .brand { left: 62px; top: 150px; }
  .card--back .brand { left: 50px; top: 110px; }
  .person { position: absolute; left: 56px; top: 192px; }
  .person-name { font-size: 18px; font-weight: 400; letter-spacing: 0.5px; }
  .person-role { font-size: 15px; font-weight: 400; margin-top: 2px; }
  .contact-list { position: absolute; left: 56px; top: 262px; list-style: none; }
  .contact-item { display: flex; align-items: center; gap: 10px; font-size: 15px; font-weight: 400; line-height: 24px; }
  .contact-icon { width: 15px; height: 15px; flex: none; }
</style>
</head>
<body>
<main class="stage">
  <section class="card card--front">
    <div class="figure-art" role="img" aria-label="Illustration of a human figure in profile with the spine highlighted"></div>
    <div class="brand">
      <span class="brand-name">QAMBRO</span>
      <span class="brand-tagline">THERAPEUTICS</span>
    </div>
  </section>

  <section class="card card--back">
    <div class="figure-art" role="img" aria-label="Illustration of a human figure in profile with the spine highlighted"></div>
    <div class="brand">
      <span class="brand-name">QAMBRO</span>
      <span class="brand-tagline">THERAPEUTICS</span>
    </div>
    <div class="person">
      <p class="person-name">DANIEL HARPER</p>
      <p class="person-role">Managing Director</p>
    </div>
    <ul class="contact-list">
      <li class="contact-item">
        <svg class="contact-icon" viewBox="0 0 16 16" aria-hidden="true"><path fill="#fff" d="M3.5 1.5l2.5 2.7-1.3 1.6c.9 2 2.5 3.6 4.5 4.5l1.6-1.3 2.7 2.5-1.7 2.2C6.5 13.1 2.9 9.5 1.3 4.2z"/></svg>
        <span>055-210 387 614</span>
      </li>
      <li class="contact-item">
        <svg class="contact-icon" viewBox="0 0 16 16" aria-hidden="true"><rect x="1" y="3" width="14" height="10" fill="#fff"/><path d="M1 3l7 5.5L15 3" fill="none" stroke="#2f8acb" stroke-width="1.3"/></svg>
        <span>hello@qambrocare.com</span>
      </li>
      <li class="contact-item">
        <svg class="contact-icon" viewBox="0 0 16 16" aria-hidden="true"><g fill="none" stroke="#fff" stroke-width="1.4"><circle cx="8" cy="8" r="6.5"/><ellipse cx="8" cy="8" rx="2.8" ry="6.5"/><path d="M1.5 8h13M2.5 4.8h11M2.5 11.2h11"/></g></svg>
        <span>www.qambrocare.com</span>
      </li>
    </ul>
  </section>
</main>
</body>
</html>
```